MRT Property - Business Cards

Looking for a business card & general letterhead, signage etc design for our new logo.

Colours:
000a20
0056a2
00b5ef
0088ce
68cef2

Fonts:
Poppins
Karla

Please keep look and feel of new brand - example in the zip package I sent.

```html
<!DOCTYPE html>
<html lang="en">
<head>
<meta charset="utf-8">
<title>MRT Property – Business Cards</title>
<link rel="stylesheet" href="https://fonts.googleapis.com/css2?family=Poppins:wght@300;400;600;700&display=swap">
<style>
  :root {
    --ink: #000a20;
    --brand-blue: #0056a2;
    --bright-blue: #00b5ef;
    --mid-blue: #0088ce;
    --sky-blue: #68cef2;
    --paper: #ffffff;
    --stage: #2e2f31;
  }
  * { box-sizing: border-box; margin: 0; padding: 0; }
  html, body {
    width: 1200px; height: 900px; overflow: hidden;
    background: var(--stage);
    font-family: "Poppins", sans-serif;
  }
  .sheet {
    width: 1200px; height: 900px;
    display: flex; align-items: center; justify-content: center; gap: 30px;
  }
  .card {
    position: relative;
    width: 560px; height: 320px;
    border-radius: 16px;
    overflow: hidden;
  }

  /* Front */
  .card--front { background: var(--paper); }
  .front__brand {
    position: absolute; top: 52px; left: 0; right: 0;
    display: flex; align-items: center; justify-content: center; gap: 12px;
  }
  .brand-dot {
    width: 26px; height: 26px; border-radius: 50%;
    background: var(--mid-blue);
  }
  .brand-name {
    font-weight: 700; font-size: 40px; letter-spacing: 0.5px;
    color: var(--brand-blue); line-height: 1;
  }
  .front__band {
    position: absolute; left: 0; right: 0; top: 150px; height: 92px;
    background: var(--brand-blue);
    display: flex; align-items: center; justify-content: space-between;
    padding: 0 30px;
  }
  .person__name {
    font-weight: 700; font-size: 24px; text-transform: uppercase;
    color: var(--bright-blue); letter-spacing: 0.5px; line-height: 1.1;
  }
  .person__role {
    font-weight: 300; font-size: 14px; color: var(--paper);
  }
  .band__mark {
    width: 54px; height: 54px; border-radius: 50%;
    background: var(--sky-blue); border: 3px solid var(--paper);
  }
  .contact { list-style: none; color: var(--paper); font-size: 13px; font-weight: 400; }
  .contact li { display: flex; align-items: center; gap: 7px; line-height: 1.5; }
  .contact svg { width: 12px; height: 12px; flex: none; }
  .front__address {
    position: absolute; left: 0; right: 0; bottom: 34px;
    text-align: center; font-size: 14px; font-weight: 400; color: var(--ink);
  }

  /* Back */
  .card--back {
    background: linear-gradient(120deg, #00397a 0%, var(--brand-blue) 45%, #0a6fd0 100%);
  }
  .back__brand {
    position: absolute; right: 44px; bottom: 110px;
    display: flex; align-items: center; gap: 14px;
  }
  .back__brand .brand-dot { background: var(--sky-blue); width: 34px; height: 34px; }
  .back__brand .brand-name { color: var(--paper); font-size: 44px; }
</style>
</head>
<body>
<main class="sheet">

  <section class="card card--front" aria-label="Business card front">
    <div class="front__brand">
      <span class="brand-dot"></span>
      <span class="brand-name">MRT Property</span>
    </div>

    <div class="front__band">
      <div class="person">
        <p class="person__name">Dana Whitley</p>
        <p class="person__role">Founder &amp; Principal</p>
      </div>
      <span class="band__mark"></span>
      <ul class="contact">
        <li>
          <svg viewBox="0 0 24 24" fill="none" stroke="currentColor" stroke-width="2"><path d="M5 3h4l2 5-3 2a12 12 0 0 0 6 6l2-3 5 2v4a2 2 0 0 1-2 2A17 17 0 0 1 3 5a2 2 0 0 1 2-2z"/></svg>
          +1- 415-555-0142
        </li>
        <li>
          <svg viewBox="0 0 24 24" fill="none" stroke="currentColor" stroke-width="2"><rect x="2" y="5" width="20" height="14" rx="1"/><path d="M2 6l10 7 10-7"/></svg>
          info@mrtproperty.com
        </li>
        <li>
          <svg viewBox="0 0 24 24" fill="none" stroke="currentColor" stroke-width="2"><circle cx="12" cy="12" r="10"/><path d="M2 12h20M12 2c3 3 3 17 0 20M12 2c-3 3-3 17 0 20"/></svg>
          www.mrtproperty.com
        </li>
      </ul>
    </div>

    <p class="front__address">4820 North Linden Avenue #12, Suite Fairview Park</p>
  </section>

  <section class="card card--back" aria-label="Business card back">
    <div class="back__brand">
      <span class="brand-dot"></span>
      <span class="brand-name">MRT Property</span>
    </div>
  </section>

</main>
</body>
</html>
```